Maple Lantern Productions web site

I need to build a website for a new company I am launching next month. Maple Lantern Productions is a company based in New England that provides sound, lighting, and audio visual services to weddings, corporate, and any other cusomer base looking for quality service for a fair price. Looking for somebody to do a full site not just the image files. I am looking to keep the colors of my logo (orange and black) and possibly grey and white. I am looking to build my site very similar to brightvaleevents.example, which is owned by a friend of mine. I like how he has the big pictures that load in to the site and the basic menu items. I'll need a gallery of photos. The designs should communicate quality, value and trust.
My website address is maplelanternco.example.
Updates

Hi and thanks to everyone for posting such great ideas for our new design.I have some items that I'd like to ask you all to focus on in your revisions.I like how http://www.brightvaleevents.example/ website has five or six high res pictures that change in a slideshow format with a caption that loads in for each one for the different types of services. Try and capture pics like these and with teh same headings as he has. The basic menu designs have been interesting.I am more fond of the menus that are more white with some orange as I dont want it to be too dark. I'm curious to see how your galleries will work and if i'll be able to edit the pages myself? I have some more info on the company for you to fill in:website address is ciderhouseco.comemail: info@ciderhouseco.comaddress: Maple Lantern Productions57 Littlefield StreetAvon, MA 02417"New England's finest DJ's, lighting and sound, video and more. Creating memories one perfect event at a time."Put this under the loading pictures as a tagline.About Cider HouseCider House Productions is a collection of New England's finest talent, ready to make your next event the one you've dreamed of. We have the skills and expertise to deliver your vision of your perfect event. From elegant weddings to themed mitzvah's, corporate av, videography and detail lighting, we offer all of the elements to make your event a success. Added Wednesday, March 1, 2017

Designer's Please also make sure that your design flows well on any device it is being viewed on as well. Thanks. Added Wednesday, March 1, 2017

Project Deadline Extended Reason: Hello designerThank you all very much for your hard work on our project. Im sorry but i need to extend the date of my project. Our parent conpany Rook Nine Prodactions sponsors Bay Youth Assemblies and we are currently at their leadership conference on the Cape. I will be back in on Monday and with your help will get this finished by Thursday the 16th. Thanks Added Thursday, March 9, 2017

Project Deadline Extended Reason: One of the designers is not responding so I now have to make revisions with other designers. I hope to get this website done over the weekends so please get your revisions as soon as possible. Thank you. I am also upgrading the budget another $75 to hopefully get some more interest on my project. Added Wednesday, March 15, 2017

Target Market(s)

Wedding - Corporate -

Industry/Entity Type

It Company

Coding

Coded - Design and coding required

Number of Pages Required

5+ page

Font styles to use
Sans Serif

Requirements
Must have
• Photo Gallery - I want to be able to edit it myself
Nice to have
• I like the look of my friends website brightvaleevents.example

```html
<!DOCTYPE html>
<html lang="en">
<head>
<meta charset="utf-8">
<title>Maple Lantern Productions</title>
<link href="https://fonts.googleapis.com/css2?family=Questrial&family=Open+Sans:ital,wght@0,400;0,600;1,400&display=swap" rel="stylesheet">
<style>
:root{
  --orange:#f26a2e;
  --orange-dark:#e0561c;
  --ink:#333333;
  --text:#666666;
  --muted:#999999;
  --line:#dddddd;
  --paper:#ffffff;
  --mist:#f1f1f1;
  --dark:#1d1b1c;
}
*{box-sizing:border-box;margin:0;padding:0}
html,body{width:1200px;height:3791px;overflow:hidden;background:var(--paper)}
body{font-family:"Open Sans",Arial,sans-serif;color:var(--text);position:relative}
.heading{font-family:"Questrial","Century Gothic",sans-serif;font-weight:400;color:var(--ink);text-align:center}
.chevron{display:block;margin:6px auto 0}
.section-title{font-size:36px}
.rule-title{position:relative;width:748px;margin:0 auto;text-align:center}
.rule-title::after{content:"";display:block;height:1px;background:var(--line);margin-top:4px}

/* hero */
.hero{position:absolute;left:0;top:0;width:1200px;height:628px;
  background:radial-gradient(ellipse at 50% 30%,#c7a08c 0%,#8c5a4a 35%,#4b2f33 70%,#2a1c22 100%)}
.nav{position:absolute;left:132px;top:13px;width:936px;height:56px;background:var(--paper);display:flex;align-items:center;justify-content:space-between;padding-left:10px}
.brand{display:flex;align-items:center;gap:10px;font-family:"Questrial",sans-serif;font-size:17px;color:var(--ink);text-transform:uppercase;letter-spacing:.5px}
.brand-dot{width:30px;height:30px;border-radius:50%;background:var(--orange)}
.menu{display:flex;height:100%;list-style:none}
.menu li{display:flex;align-items:center;padding:0 15px;font-size:15px;color:var(--ink);font-family:"Questrial",sans-serif}
.menu li.active{background:var(--orange);color:var(--paper)}
.caption{position:absolute;left:338px;top:318px;width:526px;height:229px;background:rgba(70,62,54,.72);border:2px solid rgba(255,255,255,.35);text-align:center;padding-top:44px}
.caption-quote{position:absolute;left:50%;top:-2px;transform:translateX(-50%);width:36px;height:36px;background:rgba(70,62,54,.9);color:var(--orange);font-size:46px;line-height:58px;font-family:Georgia,serif}
.caption h1{font-family:"Questrial",sans-serif;font-weight:400;font-size:35px;color:var(--paper)}
.caption p{font-size:14px;line-height:23px;color:#eee;width:470px;margin:8px auto 16px}
.btn-orange{display:inline-block;background:var(--orange);color:var(--paper);font-size:15px;padding:7px 30px;font-family:"Questrial",sans-serif}
.dots{position:absolute;top:597px;left:50%;transform:translateX(-50%);display:flex;gap:5px}
.dots span{width:10px;height:10px;border-radius:50%;border:1px solid #fff}
.dots span.on{background:#fff}

/* intro */
.intro{position:absolute;top:660px;left:0;width:1200px;text-align:center}
.intro h2{font-size:36px}
.intro p{width:1070px;margin:38px auto 0;font-size:13px;line-height:21px;color:var(--text)}
.btn-grey{display:inline-block;margin-top:26px;width:254px;height:44px;line-height:44px;background:#c8c8c8;color:var(--text);font-family:"Questrial",sans-serif;font-size:16px}

/* services */
.services{position:absolute;top:966px;left:0;width:1200px;height:351px;
  background:linear-gradient(90deg,#1a1819 0%,#2c2527 40%,#4a3b35 60%,#1e1b1c 100%)}
.services .heading{color:var(--paper);padding-top:30px}
.services .rule-title::after{background:rgba(255,255,255,.3)}
.service-list{display:flex;justify-content:space-between;width:1000px;margin:42px auto 0}
.service{width:210px;text-align:center;color:var(--paper)}
.service-icon{width:56px;height:56px;border-radius:50%;border:2px solid #fff;margin:0 auto;display:flex;align-items:center;justify-content:center}
.service h3{font-family:"Questrial",sans-serif;font-weight:400;font-size:15px;margin:18px 0 10px}
.service p{font-size:10px;line-height:15px;color:#ddd}

/* recent work */
.recent{position:absolute;top:1350px;left:0;width:1200px}
.cards{display:grid;grid-template-columns:repeat(3,300px);gap:53px 19px;justify-content:center;margin-top:45px}
.card{border:1px solid var(--line);background:var(--paper);height:384px}
.card-photo{height:229px}
.card h3{font-family:"Questrial",sans-serif;font-weight:400;color:var(--orange);font-size:19px;text-align:center;margin:14px 0 10px}
.card p{border-top:1px solid var(--line);font-size:10px;line-height:16px;text-align:center;padding:10px 22px 12px;color:var(--text)}
.card-meta{display:flex;border-top:1px solid var(--line)}
.card-meta span{flex:1;display:flex;align-items:center;justify-content:center;gap:5px;font-size:12px;height:32px;color:var(--ink)}
.card-meta span+span{border-left:1px solid var(--line)}

/* gallery */
.gallery{position:absolute;top:2295px;left:0;width:1200px}
.filters{display:flex;justify-content:center;gap:2px;margin-top:44px}
.filters span{background:#eeeeee;font-size:12px;padding:0 8px;height:33px;line-height:33px;color:var(--ink)}
.filters span.on{background:var(--orange);color:var(--paper)}
.grid{display:grid;grid-template-columns:repeat(4,218px);gap:23px 18px;justify-content:center;margin-top:35px}
.tile{height:217px;border:4px solid #fff;box-shadow:0 0 0 1px #ccc;position:relative}
.view-all{position:absolute;inset:0;display:flex;align-items:center;justify-content:center;background:rgba(80,80,80,.55);color:#fff;font-size:15px;font-family:"Questrial",sans-serif}
.view-all span{border-bottom:1px solid #fff;padding:0 18px 6px}

/* testimonial */
.testimonial{position:absolute;top:2964px;left:0;width:1200px;height:402px;background:var(--mist);text-align:center}
.avatar{width:112px;height:112px;border-radius:50%;margin:43px auto 0;border:4px solid #fff;background:linear-gradient(160deg,#a38a7b,#5b4c49)}
.stars{color:#f4b400;font-size:17px;letter-spacing:2px;margin-top:8px}
.testimonial blockquote{width:800px;margin:8px auto 0;font-style:italic;font-size:14px;line-height:22px;color:var(--muted)}
.byline{margin-top:14px;font-size:12px;color:var(--muted)}
.byline b{color:var(--orange);font-weight:600}
.quote-rule{position:relative;width:500px;height:1px;background:#999;margin:46px auto 0}
.quote-rule i{position:absolute;top:-6px;width:12px;height:12px;border-radius:50%;background:var(--orange)}

/* footer */
.footer{position:absolute;top:3366px;left:0;width:1200px}
.social{display:flex;justify-content:center;gap:7px;padding-top:38px}
.social span{width:26px;height:26px;background:#777;border-radius:3px}
.footer-rule{width:936px;height:1px;background:var(--line);margin:22px auto 0}
.columns{display:grid;grid-template-columns:repeat(4,248px);width:992px;margin:52px auto 0;padding-left:0}
.columns h4{font-family:"Questrial",sans-serif;font-weight:400;color:var(--orange);font-size:17px;margin-bottom:10px}
.columns li{list-style:none;font-size:12px;line-height:31px;color:var(--ink)}
.copyright{position:absolute;top:375px;width:1200px;text-align:center;font-size:11px;color:var(--ink)}
.copyright::before{content:"";display:block;width:936px;height:1px;background:var(--line);margin:0 auto 22px}
</style>
</head>
<body>

<header class="hero" role="img" aria-label="Hero photo: bride and groom dancing at a lively wedding reception under stage lights">
  <nav class="nav">
    <div class="brand"><span class="brand-dot"></span>Maple Lantern</div>
    <ul class="menu">
      <li class="active">Home</li><li>About Us</li><li>Our Services</li><li>Blog</li><li>Contact Us</li>
    </ul>
  </nav>
  <div class="caption">
    <span class="caption-quote">&ldquo;</span>
    <h1>Beautiful Wedding Events</h1>
    <p>Lorem Ipsum is simply dummy text of the printing and typesetting industry. Lorem Ipsum has beenLorem Ipsum is simply dummy text.</p>
    <span class="btn-orange">Contact US</span>
  </div>
  <div class="dots"><span class="on"></span><span></span><span></span></div>
</header>

<section class="intro">
  <h2 class="heading">Maple Lantern are Experts in All Type of Events</h2>
  <svg class="chevron" width="20" height="10" viewBox="0 0 20 10"><path d="M2 2l8 6 8-6" fill="none" stroke="#999" stroke-width="1.5"/></svg>
  <p>Lorem Ipsum is simply dummy text of the printing and typesetting industry. Lorem Ipsum has been the industry's standard dummy text ever since the 1500s, when an unknown printer took a galley of type and scrambled it to make a type specimen book. It has survived not only five centuries, but also the leap into electronic typesetting, remaining essentially unchanged. It was popularised in the</p>
  <span class="btn-grey">How can we help you ?</span>
</section>

<section class="services" role="img" aria-label="Background photo: guests raising glasses at a dim evening event">
  <div class="rule-title"><h2 class="heading section-title" style="color:#fff">Our Services</h2></div>
  <svg class="chevron" width="20" height="10" viewBox="0 0 20 10"><path d="M2 2l8 6 8-6" fill="none" stroke="#ccc" stroke-width="1.5"/></svg>
  <div class="service-list">
    <div class="service">
      <div class="service-icon"><svg width="24" height="20" viewBox="0 0 24 20"><rect x="2" y="5" width="20" height="13" rx="2" fill="#fff"/><rect x="8" y="1" width="8" height="5" rx="1" fill="none" stroke="#fff" stroke-width="2"/></svg></div>
      <h3>Corporate Events</h3>
      <p>Lorem Ipsum is simply dummy text of the printing and typesetting industry. Lorem Ipsum has been the industry's</p>
    </div>
    <div class="service">
      <div class="service-icon"><svg width="24" height="24" viewBox="0 0 24 24"><circle cx="9" cy="15" r="6" fill="#fff"/><path d="M12 12L21 3" stroke="#fff" stroke-width="2.5"/></svg></div>
      <h3>Music Concert</h3>
      <p>Lorem Ipsum is simply dummy text of the printing and typesetting industry. Lorem Ipsum has been the industry's</p>
    </div>
    <div class="service">
      <div class="service-icon"><svg width="28" height="20" viewBox="0 0 28 20"><circle cx="10" cy="11" r="7" fill="none" stroke="#fff" stroke-width="2.5"/><circle cx="18" cy="11" r="7" fill="none" stroke="#fff" stroke-width="2.5"/></svg></div>
      <h3>Wedding Plane</h3>
      <p>Lorem Ipsum is simply dummy text of the printing and typesetting industry. Lorem Ipsum has been the industry's</p>
    </div>
    <div class="service">
      <div class="service-icon"><svg width="28" height="20" viewBox="0 0 28 20"><path d="M14 2L27 8 14 14 1 8z" fill="#fff"/><path d="M7 11v5c4 3 10 3 14 0v-5" fill="#fff"/></svg></div>
      <h3>School and Formal Events</h3>
      <p>Lorem Ipsum is simply dummy text of the printing and typesetting industry. Lorem Ipsum has been the industry's</p>
    </div>
  </div>
</section>

<section class="recent">
  <div class="rule-title"><h2 class="heading section-title">Recent Work</h2></div>
  <svg class="chevron" width="20" height="10" viewBox="0 0 20 10"><path d="M2 2l8 6 8-6" fill="none" stroke="#999" stroke-width="1.5"/></svg>
  <div class="cards">
    <article class="card">
      <div class="card-photo" role="img" aria-label="Photo: audience seated at a corporate conference with speaker on stage" style="background:linear-gradient(180deg,#c9b9b0,#7a4a3a 60%,#3a2a26)"></div>
      <h3>Corporate Events</h3>
      <p>Lorem Ipsum is simply dummy text of the printing and typesetting industry. Lorem Ipsum has been the industry's standard dummy text ever</p>
      <div class="card-meta"><span><svg width="12" height="10" viewBox="0 0 12 10"><rect x="0" y="2" width="12" height="8" rx="1" fill="#f26a2e"/><circle cx="6" cy="6" r="2" fill="#fff"/></svg>See Photo</span><span><svg width="9" height="12" viewBox="0 0 9 12"><path d="M4.5 12C1 7 0 5.5 0 4.5a4.5 4.5 0 019 0C9 5.5 8 7 4.5 12z" fill="#f26a2e"/><circle cx="4.5" cy="4.5" r="1.6" fill="#fff"/></svg>See Location</span></div>
    </article>
    <article class="card">
      <div class="card-photo" role="img" aria-label="Photo: newlyweds celebrating outdoors with guests" style="background:linear-gradient(160deg,#e8d28a,#b89a64 50%,#6f7a4a)"></div>
      <h3>Wedding Event</h3>
      <p>Lorem Ipsum is simply dummy text of the printing and typesetting industry. Lorem Ipsum has been the industry's standard dummy text ever</p>
      <div class="card-meta"><span><svg width="12" height="10" viewBox="0 0 12 10"><rect x="0" y="2" width="12" height="8" rx="1" fill="#f26a2e"/><circle cx="6" cy="6" r="2" fill="#fff"/></svg>See Photo</span><span><svg width="9" height="12" viewBox="0 0 9 12"><path d="M4.5 12C1 7 0 5.5 0 4.5a4.5 4.5 0 019 0C9 5.5 8 7 4.5 12z" fill="#f26a2e"/><circle cx="4.5" cy="4.5" r="1.6" fill="#fff"/></svg>See Location</span></div>
    </article>
    <article class="card">
      <div class="card-photo" role="img" aria-label="Photo: teenagers dancing at a high school party" style="background:linear-gradient(160deg,#e9c24a,#c7692e 55%,#6b2a1c)"></div>
      <h3>High School Party</h3>
      <p>Lorem Ipsum is simply dummy text of the printing and typesetting industry. Lorem Ipsum has been the industry's standard dummy text ever</p>
      <div class="card-meta"><span><svg width="12" height="10" viewBox="0 0 12 10"><rect x="0" y="2" width="12" height="8" rx="1" fill="#f26a2e"/><circle cx="6" cy="6" r="2" fill="#fff"/></svg>See Photo</span><span><svg width="9" height="12" viewBox="0 0 9 12"><path d="M4.5 12C1 7 0 5.5 0 4.5a4.5 4.5 0 019 0C9 5.5 8 7 4.5 12z" fill="#f26a2e"/><circle cx="4.5" cy="4.5" r="1.6" fill="#fff"/></svg>See Location</span></div>
    </article>
    <article class="card">
      <div class="card-photo" role="img" aria-label="Photo: concert crowd with raised hands under blue stage lights" style="background:linear-gradient(180deg,#9fb8ea,#3a56b0 50%,#0c1430)"></div>
      <h3>Music Concert</h3>
      <p>Lorem Ipsum is simply dummy text of the printing and typesetting industry. Lorem Ipsum has been the industry's standard dummy text ever</p>
      <div class="card-meta"><span><svg width="12" height="10" viewBox="0 0 12 10"><rect x="0" y="2" width="12" height="8" rx="1" fill="#f26a2e"/><circle cx="6" cy="6" r="2" fill="#fff"/></svg>See Photo</span><span><svg width="9" height="12" viewBox="0 0 9 12"><path d="M4.5 12C1 7 0 5.5 0 4.5a4.5 4.5 0 019 0C9 5.5 8 7 4.5 12z" fill="#f26a2e"/><circle cx="4.5" cy="4.5" r="1.6" fill="#fff"/></svg>See Location</span></div>
    </article>
    <article class="card">
      <div class="card-photo" role="img" aria-label="Photo: friends toasting with drinks at a bar celebration" style="background:linear-gradient(160deg,#c7774a,#7a2f1e 55%,#2a1410)"></div>
      <h3>Bar / Bal Mitzvahs</h3>
      <p>Lorem Ipsum is simply dummy text of the printing and typesetting industry. Lorem Ipsum has been the industry's standard dummy text ever</p>
      <div class="card-meta"><span><svg width="12" height="10" viewBox="0 0 12 10"><rect x="0" y="2" width="12" height="8" rx="1" fill="#f26a2e"/><circle cx="6" cy="6" r="2" fill="#fff"/></svg>See Photo</span><span><svg width="9" height="12" viewBox="0 0 9 12"><path d="M4.5 12C1 7 0 5.5 0 4.5a4.5 4.5 0 019 0C9 5.5 8 7 4.5 12z" fill="#f26a2e"/><circle cx="4.5" cy="4.5" r="1.6" fill="#fff"/></svg>See Location</span></div>
    </article>
    <article class="card">
      <div class="card-photo" role="img" aria-label="Photo: children with balloons at a birthday party" style="background:linear-gradient(160deg,#e44a3a,#e9b23c 45%,#4a8fd0)"></div>
      <h3>Birthdays Party</h3>
      <p>Lorem Ipsum is simply dummy text of the printing and typesetting industry. Lorem Ipsum has been the industry's standard dummy text ever</p>
      <div class="card-meta"><span><svg width="12" height="10" viewBox="0 0 12 10"><rect x="0" y="2" width="12" height="8" rx="1" fill="#f26a2e"/><circle cx="6" cy="6" r="2" fill="#fff"/></svg>See Photo</span><span><svg width="9" height="12" viewBox="0 0 9 12"><path d="M4.5 12C1 7 0 5.5 0 4.5a4.5 4.5 0 019 0C9 5.5 8 7 4.5 12z" fill="#f26a2e"/><circle cx="4.5" cy="4.5" r="1.6" fill="#fff"/></svg>See Location</span></div>
    </article>
  </div>
</section>

<section class="gallery">
  <h2 class="heading section-title">Photo Gallery</h2>
  <svg class="chevron" width="20" height="10" viewBox="0 0 20 10"><path d="M2 2l8 6 8-6" fill="none" stroke="#999" stroke-width="1.5"/></svg>
  <div class="filters">
    <span class="on">All</span><span>Corporate Events</span><span>Wedding Events</span><span>Music Concert</span><span>Bar / Bal Mitzvahs</span><span>Birthday Party</span><span>High School Party</span>
  </div>
  <div class="grid">
    <div class="tile" role="img" aria-label="Photo: dancers under purple party lights" style="background:linear-gradient(160deg,#6a4fc0,#2a2a8a 60%,#1a1440)"></div>
    <div class="tile" role="img" aria-label="Photo: children around a birthday cake with balloons" style="background:linear-gradient(160deg,#f0c860,#e08a4a 50%,#b44a3a)"></div>
    <div class="tile" role="img" aria-label="Photo: wedding couple in black and white" style="background:linear-gradient(160deg,#bbbbbb,#555555)"><div class="view-all"><span>View All</span></div></div>
    <div class="tile" role="img" aria-label="Photo: friends clinking glasses" style="background:linear-gradient(160deg,#d08a5a,#6a2e20)"></div>
    <div class="tile" role="img" aria-label="Photo: bride and groom embracing outdoors" style="background:linear-gradient(160deg,#e9eef2,#a8b4c0 60%,#6f7f8a)"></div>
    <div class="tile" role="img" aria-label="Photo: guests applauding at an evening event" style="background:linear-gradient(160deg,#c65a2e,#5a2418 60%,#1e100c)"></div>
    <div class="tile" role="img" aria-label="Photo: presenter on stage at a corporate conference" style="background:linear-gradient(160deg,#d8a070,#7a4a34 55%,#2e1e1a)"></div>
    <div class="tile" role="img" aria-label="Photo: floral wedding arch by the sea" style="background:linear-gradient(180deg,#cfe2f0,#e6d4e6 55%,#a8b87a)"></div>
  </div>
</section>

<section class="testimonial">
  <div class="avatar" role="img" aria-label="Portrait of client giving the testimonial"></div>
  <div class="stars">&#9733;&#9733;&#9733;&#9733;&#9733;</div>
  <blockquote>Lorem Ipsum is simply dummy text of the printing and typesetting industry. Lorem Ipsum has been the industry's standard dummy text ever since the 1500s, when an unknown printer took a galley of type and scrambled it to make a type s survived not only five centuries, but also the leap into</blockquote>
  <p class="byline"><b>rowan pike</b> &bull; 17/Mob/2018</p>
  <div class="quote-rule"><i style="left:238px"></i><i style="left:252px"></i></div>
</section>

<footer class="footer">
  <div class="social"><span></span><span></span><span></span><span></span><span></span></div>
  <div class="footer-rule"></div>
  <div class="columns">
    <div><h4>News &amp; Media</h4><ul><li>Latest Stories</li><li>Press Releases</li><li>Media Inquiries</li><li>Media Partners</li><li>The News</li></ul></div>
    <div><h4>Support</h4><ul><li>Latest Stories</li><li>Press Releases</li><li>Media Inquiries</li><li>Media Partners</li><li>The News</li></ul></div>
    <div><h4>Event</h4><ul><li>Latest Stories</li><li>Press Releases</li><li>Media Inquiries</li><li>Media Partners</li><li>The News</li></ul></div>
    <div><h4>News &amp; Media</h4><ul><li>Submit Your Story</li><li>Member Updates Archive</li><li>Contact</li><li>Login</li></ul></div>
  </div>
  <p class="copyright">&copy; maplelanternco.example, 2017. All Rights reserved. &nbsp;Privacy Policy</p>
</footer>

</body>
</html>
```